Mobile Fitness snd Therapy Business Card Design

I need a business card designed for my mobile fitness and therapy business.

Please view the images that I have uploaded. I like the simplicity of the design that I have attached. I adapted it with my information

Target Market(s)

Those seeking personal training, injury rehabilitation or massage therapy.

Industry/Entity Type

Business

Contact Information for Business Card

Derek Fulham - MSc, CAT(C), RMT, CSCS, Pn2
e-mail: derek@vantrelo.com
website: www.vantrelo.com
instagram: @derek_fulham

Font styles to use
Sans Serif

Colors
3176b5
0355a3

Requirements
Must have
• "Contact us to receive a FREE assessment"
• Services offered:
• Personal Training
• Golf Fitness
• Injury Rehab
• Massage Therapy
• Yoga
Nice to have
• Consistent colours with brand
• - Dark Blue: #232837
• - Blue: #5096f0
• Consistent look/feel with the website: www.vantrelo.com

```html
<!DOCTYPE html>
<html lang="en">
<head>
<meta charset="utf-8">
<title>Vantrelo Business Card</title>
<link rel="stylesheet" href="https://fonts.googleapis.com/css2?family=Open+Sans:wght@400;600;700&display=swap">
<style>
  :root {
    --page-bg: #e9e7e4;
    --card-white: #f7f6f5;
    --navy: #232837;
    --ink: #2a2f3d;
    --accent-blue: #2a5bd7;
    --strip-blue: #2f62d6;
    --white: #ffffff;
  }
  * { margin: 0; padding: 0; box-sizing: border-box; }
  html, body {
    width: 1200px; height: 900px; overflow: hidden;
    background: var(--page-bg);
    font-family: "Open Sans", Arial, sans-serif;
  }
  .card {
    position: absolute; left: 120px; top: 152px;
    width: 960px; height: 596px;
    border-radius: 16px; overflow: hidden;
    display: flex;
    box-shadow: 0 18px 40px rgba(0,0,0,0.18);
  }
  .card-front {
    position: relative; width: 477px; height: 100%;
    background: var(--card-white);
  }
  .brand { position: absolute; left: 34px; top: 52px; }
  .brand-name {
    font-weight: 700; font-size: 50px; line-height: 1;
    letter-spacing: 5px; color: var(--ink);
  }
  .brand-tagline {
    margin-top: 10px; font-weight: 700; font-size: 17px;
    letter-spacing: 2.2px; color: var(--ink);
  }
  .contact { position: absolute; left: 36px; top: 352px; color: #333; }
  .contact-name {
    font-weight: 600; font-size: 33px; color: var(--accent-blue); line-height: 1.1;
  }
  .contact-credentials { font-size: 21px; margin-top: 4px; }
  .contact-lines { margin-top: 22px; font-size: 26px; line-height: 1.32; }
  .offer-strip {
    position: relative; width: 69px; height: 100%;
    background: var(--strip-blue);
  }
  .offer-text {
    position: absolute; left: 50%; top: 50%;
    transform: translate(-50%, -50%) rotate(-90deg);
    white-space: nowrap; color: var(--white);
    font-size: 26px; letter-spacing: 0.3px;
  }
  .card-back {
    position: relative; flex: 1; height: 100%;
    background: var(--navy); color: var(--white);
  }
  .card-back .brand { left: 37px; top: 36px; }
  .card-back .brand-name { color: var(--white); font-size: 46px; letter-spacing: 4px; }
  .card-back .brand-tagline { color: var(--white); font-size: 15px; letter-spacing: 2px; margin-top: 8px; }
  .services-title {
    position: absolute; left: 65px; top: 178px;
    font-weight: 600; font-size: 31px; text-decoration: underline;
    text-underline-offset: 5px; text-decoration-thickness: 2px;
  }
  .service-list {
    position: absolute; left: 37px; top: 246px; list-style: none;
  }
  .service-item {
    display: flex; align-items: center; gap: 16px;
    font-weight: 600; font-size: 36px; height: 64.5px;
  }
  .service-star { width: 28px; height: 28px; flex: none; }
</style>
</head>
<body>
  <div class="card">
    <section class="card-front">
      <div class="brand">
        <div class="brand-name">VANTRELO</div>
        <div class="brand-tagline">NUTRITION - FITNESS - HEALTH</div>
      </div>
      <div class="contact">
        <div class="contact-name">DEREK FULHAM</div>
        <div class="contact-credentials">MSc, CAT(C), RMT, CSCS, Pn2</div>
        <div class="contact-lines">
          <div>e-mail: derek@vantrelo.com</div>
          <div>website: www.vantrelo.com</div>
          <div>instagram: @derek_fulham</div>
        </div>
      </div>
    </section>
    <div class="offer-strip">
      <div class="offer-text">Contact us to receive a FREE assessment</div>
    </div>
    <section class="card-back">
      <div class="brand">
        <div class="brand-name">VANTRELO</div>
        <div class="brand-tagline">NUTRITION - FITNESS - HEALTH</div>
      </div>
      <div class="services-title">SERVICES OFFERED</div>
      <ul class="service-list">
        <li class="service-item"><svg class="service-star" viewBox="0 0 24 24"><path fill="#fff" d="M12 1.5l3.1 6.9 7.4.7-5.6 5 1.7 7.4L12 17.6l-6.6 3.9 1.7-7.4-5.6-5 7.4-.7z"/></svg>Personal Training</li>
        <li class="service-item"><svg class="service-star" viewBox="0 0 24 24"><path fill="#fff" d="M12 1.5l3.1 6.9 7.4.7-5.6 5 1.7 7.4L12 17.6l-6.6 3.9 1.7-7.4-5.6-5 7.4-.7z"/></svg>Golf Fitness</li>
        <li class="service-item"><svg class="service-star" viewBox="0 0 24 24"><path fill="#fff" d="M12 1.5l3.1 6.9 7.4.7-5.6 5 1.7 7.4L12 17.6l-6.6 3.9 1.7-7.4-5.6-5 7.4-.7z"/></svg>Injury Rehab</li>
        <li class="service-item"><svg class="service-star" viewBox="0 0 24 24"><path fill="#fff" d="M12 1.5l3.1 6.9 7.4.7-5.6 5 1.7 7.4L12 17.6l-6.6 3.9 1.7-7.4-5.6-5 7.4-.7z"/></svg>Massage Therapy</li>
        <li class="service-item"><svg class="service-star" viewBox="0 0 24 24"><path fill="#fff" d="M12 1.5l3.1 6.9 7.4.7-5.6 5 1.7 7.4L12 17.6l-6.6 3.9 1.7-7.4-5.6-5 7.4-.7z"/></svg>Yoga</li>
      </ul>
    </section>
  </div>
</body>
</html>
```